Business Cards used to invite people to our church

We are a church and have need of a business card sized advertisement that allows our members to hand them out in order to invite people to the church. I need the front of the card to say "You're Invited" or "Come Check us out". with the service times on the back of the card later.
I have attached one of the OLD cards we have used in the past, but we want a complete makeover, into a more modern style that does not require the image.
I am also replacing the old logo with a newer "flat" logo which is attached.
Please use marketing colors. (blue or red or something that catches attention)
Create a card that DOES NOT have the picture of the two people on the front
The information on the sample card back is correct to go onto new card
Target Market(s)
anyone
Industry/Entity Type
Business
Contact Information for Business Card
sertice times and address information which you can get from the sample card I uploaded. It should have "You're Invited" or "Come Check us out" on the front of the card with out logo.

```html
<!DOCTYPE html>
<html lang="en">
<head>
<meta charset="utf-8">
<title>Grace Harbor Ministries – Invitation Card</title>
<link href="https://fonts.googleapis.com/css2?family=Montserrat:wght@400;600;700&display=swap" rel="stylesheet">
<style>
  :root {
    --backdrop: #9c9c9a;
    --card: #0b0b0b;
    --card-edge: #1c1c1c;
    --ink: #ffffff;
    --ink-soft: #e6e6e6;
  }
  * { box-sizing: border-box; margin: 0; padding: 0; }
  html, body {
    width: 1200px; height: 900px; overflow: hidden;
    background: var(--backdrop);
    font-family: "Montserrat", Arial, sans-serif;
  }
  .canvas {
    position: relative; width: 1200px; height: 900px;
  }
  .card {
    position: absolute; left: 280px;
    width: 640px; height: 366px;
    background: radial-gradient(ellipse at 40% 35%, var(--card-edge) 0%, var(--card) 70%);
    color: var(--ink);
    border-radius: 3px;
    box-shadow: 0 6px 18px rgba(0,0,0,0.25);
  }
  .card--back { top: 54px; }
  .card--front { top: 480px; }

  /* Back side: ministry details */
  .ministry {
    position: absolute; top: 58px; left: 0; right: 0;
    text-align: center;
  }
  .ministry__name {
    display: inline-flex; align-items: center; gap: 14px;
    font-size: 26px; font-weight: 600; letter-spacing: 3px;
    text-transform: uppercase; color: var(--ink);
  }
  .ministry__mark {
    width: 22px; height: 22px; background: var(--ink);
  }
  .ministry__address {
    margin-top: 30px;
    font-size: 15px; font-weight: 700; color: var(--ink);
  }
  .ministry__phone {
    margin-top: 6px;
    font-size: 15px; font-weight: 700; color: var(--ink);
  }
  .schedule {
    list-style: none;
    position: absolute; left: 150px; width: 340px; top: 200px;
    font-size: 14px; color: var(--ink-soft);
  }
  .schedule__row {
    display: flex; align-items: baseline; margin-bottom: 10px;
  }
  .schedule__leader {
    flex: 1; border-bottom: 1px dotted var(--ink-soft);
    margin: 0 4px; transform: translateY(-4px);
  }

  /* Front side: invitation */
  .invite__word {
    position: absolute;
    font-size: 40px; font-weight: 400; letter-spacing: 1px;
    color: var(--ink);
  }
  .invite__word--come  { left: 80px;  top: 52px; }
  .invite__word--check { left: 180px; top: 130px; }
  .invite__word--us    { left: 330px; top: 210px; }
  .invite__word--out   { left: 430px; top: 285px; }
</style>
</head>
<body>
<main class="canvas">
  <section class="card card--back" aria-label="Card back">
    <header class="ministry">
      <div class="ministry__name"><span class="ministry__mark"></span>Grace Harbor Ministries</div>
      <p class="ministry__address">2740 Willow Lane - Ashford, Tx 75000</p>
      <p class="ministry__phone">1-800-555-0182</p>
    </header>
    <ul class="schedule">
      <li class="schedule__row"><span>Sunday</span><span class="schedule__leader"></span><span>9:00 Am</span></li>
      <li class="schedule__row"><span>Sunday</span><span class="schedule__leader"></span><span>11:00 Am</span></li>
      <li class="schedule__row"><span>Wed. Bible Class</span><span class="schedule__leader"></span><span>7:00 Pm</span></li>
    </ul>
  </section>

  <section class="card card--front" aria-label="Card front">
    <h1 class="invite">
      <span class="invite__word invite__word--come">Come</span>
      <span class="invite__word invite__word--check">Check</span>
      <span class="invite__word invite__word--us">us</span>
      <span class="invite__word invite__word--out">out</span>
    </h1>
  </section>
</main>
</body>
</html>
```